Valmora Health a direct primary care practice needs a beautiful and customer friendly website

We need a website to showcase our new medical practice. We want to enhance the customer experience and make it easy to navigate to the desired page by placing pillar pages on the home screen. the website needs to be clean and bright.

Target Market(s)

Uninsured, Small businesses that can't afford to offer employees insurance.

Industry/Entity Type

Healthcare

Coding

Coded - Design and coding required

Font styles to use
Serif
Sans Serif

Colors
0592cd
3377b5
0355a3
9bcb3c
acd136

Requirements
Must have
• Must be user friendly, must have pillar pages to help boost SEO ranking, clean and bright, must be close to the in colors to the attached logo.

Content will be very similar to www.quillbrookhealth.example
Nice to have
• Clean and easy to read font

```html
<!DOCTYPE html>
<html lang="en">
<head>
<meta charset="utf-8">
<title>Valmora Health — Direct Primary Care</title>
<link href="https://fonts.googleapis.com/css2?family=Poppins:wght@300;400;500;600;700;800&family=Lato:wght@400;700&display=swap" rel="stylesheet">
<style>
:root{
  --blue:#0355a3;
  --blue-mid:#3377b5;
  --blue-light:#0592cd;
  --green:#1f8a32;
  --green-light:#9bcb3c;
  --lime:#acd136;
  --ink:#1b1b1b;
  --text:#555a60;
  --footer:#23262b;
  --footer-deep:#1a1c20;
  --white:#ffffff;
}
*{margin:0;padding:0;box-sizing:border-box}
html,body{width:1200px;height:5277px;overflow:hidden;background:#fff}
body{font-family:"Lato",sans-serif;color:var(--text)}
.page{position:relative;width:1200px;height:5277px;overflow:hidden}
.abs{position:absolute}

/* header */
.topbar{top:0;left:0;width:1200px;height:106px}
.call{left:143px;top:30px;display:flex;align-items:center;gap:12px}
.call-icon{width:36px;height:36px;border-radius:50%;background:var(--green);display:flex;align-items:center;justify-content:center}
.call small{display:block;font:400 13px "Poppins",sans-serif;color:#777}
.call strong{font:700 17px "Poppins",sans-serif;color:var(--ink)}
.brand{left:0;width:1200px;top:48px;text-align:center;font:500 32px "Poppins",sans-serif;color:var(--blue)}
.join-top{left:916px;top:34px;width:140px;height:40px;border:2px solid var(--green);border-radius:20px;font:600 13px "Poppins",sans-serif;color:var(--green);display:flex;align-items:center;justify-content:center}
.nav{top:106px;left:0;width:1200px;height:54px;border-top:1px solid #e6e6e6;display:flex;justify-content:center;gap:48px;align-items:center}
.nav a{font:600 13px "Poppins",sans-serif;color:#222;text-decoration:none;letter-spacing:.3px}
.nav a.active{color:var(--green);position:relative}
.nav a.active::before{content:"";position:absolute;left:-10px;right:-10px;top:-16px;height:4px;border-radius:4px;background:var(--green)}

/* hero */
.hero{top:160px;left:0;width:1200px;height:712px;background:linear-gradient(100deg,#e7d5c8 0%,#f2e6dc 40%,#d8e2ea 70%,#c9d4dc 100%)}
.hero-title{left:140px;top:212px;font:800 48px/60px "Poppins",sans-serif;color:#15213b;text-transform:uppercase}
.btn-blue{background:var(--blue);color:#fff;font:600 15px "Poppins",sans-serif;display:flex;align-items:center;justify-content:center;border-radius:3px}
.hero-btn{left:142px;top:408px;width:196px;height:48px}
.arrow-dot{width:30px;height:30px;border-radius:50%;background:rgba(0,0,0,.45);display:flex;align-items:center;justify-content:center}

/* welcome */
.welcome-photo{left:146px;top:893px;width:376px;height:376px;border-radius:50%;background:linear-gradient(135deg,#e9c9b3,#c9a08a 55%,#8a6f66)}
.eyebrow{font:400 29px "Poppins",sans-serif;color:var(--blue)}
.section-title{font:700 38px "Poppins",sans-serif;color:var(--ink)}
.body-copy{font:400 14px/22.5px "Lato",sans-serif;color:#4d4d4d}

/* services */
.services-band{top:1380px;left:0;width:1200px;height:800px}
.services-title{top:1466px;left:0;width:1200px;text-align:center;font:700 36px "Poppins",sans-serif;color:#fff}
.hub{left:481px;top:1704px;width:238px;height:238px;border-radius:50%;background:#fff;display:flex;align-items:center;justify-content:center}
.hub b{font:500 24px "Poppins",sans-serif;color:var(--blue)}
.svc{height:147px;border:2px solid rgba(255,255,255,.85);border-radius:74px;display:flex;align-items:center;gap:18px;padding:0 22px}
.svc.left{text-align:right;justify-content:flex-end}
.svc h3{font:600 17px "Poppins",sans-serif;color:#fff;margin-bottom:6px}
.svc p{font:400 12px/17px "Lato",sans-serif;color:#e4ecf7}
.svc-icon{flex:0 0 86px;height:86px;border-radius:50%;background:linear-gradient(140deg,var(--lime),#5fae2e);display:flex;align-items:center;justify-content:center}

/* employers */
.video-frame{left:813px;top:2306px;width:242px;height:386px;background:linear-gradient(180deg,#1e9a3a,#0d6d26);border-radius:6px}
.video{left:567px;top:2333px;width:463px;height:331px;background:linear-gradient(120deg,#dfe6ea,#b9cad6 50%,#6f9cc0);border-radius:4px;box-shadow:0 6px 18px rgba(0,0,0,.25)}
.play{left:773px;top:2473px;width:50px;height:50px;border-radius:50%;background:rgba(255,255,255,.9);display:flex;align-items:center;justify-content:center}

/* testimonials */
.testi-band{top:2760px;left:0;width:1200px;height:620px}
.center-title{left:0;width:1200px;text-align:center;font:700 38px "Poppins",sans-serif}
.rule{width:58px;height:4px;border-radius:2px}
.t-card{top:2967px;width:418px;height:271px;border:2px solid rgba(255,255,255,.85);border-radius:10px;padding:20px 30px 0 34px}
.t-card .qmark{position:absolute;left:-20px;top:4px;font:700 64px/1 "Poppins",sans-serif;color:#fff}
.t-card .qend{position:absolute;right:34px;bottom:24px;font:700 64px/0.7 "Poppins",sans-serif;color:rgba(255,255,255,.5)}
.t-card p{font:400 14px/22.5px "Lato",sans-serif;color:#fff}
.t-person{display:flex;align-items:center;gap:22px;margin-top:16px}
.avatar{width:78px;height:78px;border-radius:50%;background:linear-gradient(135deg,#f1d8c9,#c9a48e);border:3px solid #fff}
.t-person b{display:block;font:500 14px "Poppins",sans-serif;color:#fff}
.t-person span{display:block;font:400 14px "Poppins",sans-serif;color:#fff}
.stars{color:#fff;font-size:14px;letter-spacing:2px}

/* blog */
.blog-card{top:3560px;width:287px;height:476px;border:1px solid #e1e1e1;background:#fff}
.blog-img{width:285px;height:225px}
.blog-body{padding:20px 22px}
.blog-date{font:600 13px "Poppins",sans-serif;color:var(--blue);display:flex;align-items:center;gap:8px}
.blog-body h4{font:600 13px/23px "Poppins",sans-serif;color:#222;margin:18px 0 10px;text-transform:uppercase}
.blog-body p{font:400 13px/20px "Lato",sans-serif;color:#666}
.btn-outline{display:inline-flex;align-items:center;justify-content:center;margin-top:18px;width:126px;height:34px;border:2px solid #222;border-radius:17px;font:700 11px "Poppins",sans-serif;color:#222}

/* quote */
.quote-band{top:4110px;left:0;width:1200px;height:640px}
.field{border:1px solid rgba(255,255,255,.75);font:400 11px "Lato",sans-serif;color:#fff;padding:14px 22px}
.submit{left:524px;top:4612px;width:152px;height:43px;background:#fff;color:var(--blue);font:600 13px "Poppins",sans-serif;display:flex;align-items:center;justify-content:center;border-radius:3px}

/* footer */
.footer{top:4720px;left:0;width:1200px;height:557px;background:var(--footer)}
.footer-logo{left:120px;top:4848px;width:320px;text-align:center;font:500 32px "Poppins",sans-serif;color:#fff}
.footer-copy{font:400 14px/24px "Lato",sans-serif;color:#d9d9d9}
.footer-heading{font:700 17px "Poppins",sans-serif;color:#fff;letter-spacing:.3px}
.social{display:flex;gap:8px}
.social span{width:32px;height:32px;border:1.5px solid #cfcfcf;border-radius:50%}
.contact-row{display:flex;gap:18px;font:400 15px/21px "Lato",sans-serif;color:#d9d9d9}
.email-box{left:752px;top:4950px;width:302px;height:46px;background:#fff;border-radius:23px;display:flex;align-items:center;padding-left:18px;font:400 13px "Lato",sans-serif;color:#777}
.email-go{position:absolute;right:5px;top:5px;width:36px;height:36px;border-radius:50%;background:var(--green-light);display:flex;align-items:center;justify-content:center}
.copyright{top:5140px;left:0;width:1200px;height:137px;background:var(--footer-deep);display:flex;align-items:center;justify-content:center;font:400 14px "Lato",sans-serif;color:#e6e6e6}
</style>
</head>
<body>
<div class="page">

  <header class="abs topbar">
    <div class="abs call">
      <div class="call-icon">
        <svg width="18" height="18" viewBox="0 0 24 24"><path fill="#fff" d="M6.6 10.8a15.1 15.1 0 0 0 6.6 6.6l2.2-2.2c.3-.3.7-.4 1-.2 1.1.4 2.3.6 3.6.6.6 0 1 .4 1 1V20c0 .6-.4 1-1 1A17 17 0 0 1 3 4c0-.6.4-1 1-1h3.5c.6 0 1 .4 1 1 0 1.3.2 2.5.6 3.6.1.3 0 .7-.2 1z"/></svg>
      </div>
      <div><small>Call Us :</small><strong>(808) 555-0142</strong></div>
    </div>
    <div class="abs brand">Valmora Health</div>
    <div class="abs join-top">JOIN US</div>
  </header>
  <nav class="abs nav">
    <a class="active">HOME</a><a>ABOUT US</a><a>OUR SERVICES</a><a>EMPLOYERS</a><a>PRICING</a><a>FAQ</a><a>BLOG</a><a>CONTACT US</a>
  </nav>

  <section class="abs hero" role="img" aria-label="Doctor listening to a smiling young girl's heartbeat with a stethoscope"></section>
  <h1 class="abs hero-title">Valmora Health<br>Healthcare<br>Reimagined</h1>
  <div class="abs btn-blue hero-btn">JOIN US</div>
  <div class="abs arrow-dot" style="left:71px;top:484px"><svg width="12" height="12" viewBox="0 0 12 12"><path d="M8 1 3 6l5 5" stroke="#fff" stroke-width="2" fill="none"/></svg></div>
  <div class="abs arrow-dot" style="left:1096px;top:484px;background:transparent"><svg width="12" height="12" viewBox="0 0 12 12"><path d="m4 1 5 5-5 5" stroke="#fff" stroke-width="2" fill="none"/></svg></div>
  <svg class="abs" style="left:0;top:740px" width="1200" height="135" viewBox="0 0 1200 135">
    <path d="M0 135 L0 120 Q600 -40 1200 120 L1200 135 Z" fill="#fff"/>
    <path d="M40 135 Q600 -60 1160 130 Q600 -20 40 135 Z" fill="var(--green)"/>
  </svg>

  <svg class="abs" style="left:140px;top:885px" width="200" height="400" viewBox="0 0 200 400">
    <path d="M200 3 A197 197 0 0 0 200 397" stroke="var(--green)" stroke-width="8" fill="none"/>
  </svg>
  <div class="abs welcome-photo" role="img" aria-label="Mother and daughter giving a high five to their doctor"></div>
  <div class="abs eyebrow" style="left:608px;top:893px">Welcome to</div>
  <h2 class="abs section-title" style="left:608px;top:930px">Valmora Health</h2>
  <p class="abs body-copy" style="left:608px;top:995px;width:445px">Sed ut perspiciatis unde omnis iste natus error sit voluptatem accusantium doloremque laudantium, totam rem aperiam, eaque ipsa quae ab illo inventore veritatis et quasi architecto beatae vitae dicta sunt explicabo. Nemo enim ipsam voluptatem quia voluptas sit aspernatur aut odit aut fugit, sed quia consequuntur magni dolores eos qui ratione voluptatem sequi nesciunt. Neque porro quisquam est, qui dolorem ipsum quia dolor sit amet, consectetur, adipisci velit, sed quia non</p>
  <div class="abs btn-blue" style="left:608px;top:1204px;width:150px;height:42px;font-size:13px">LEARN MORE</div>

  <svg class="abs services-band" viewBox="0 0 1200 800" preserveAspectRatio="none">
    <defs><linearGradient id="svcBlue" x1="0" y1="0" x2="1" y2="1"><stop offset="0" stop-color="#0a4fa0"/><stop offset="1" stop-color="#0355a3"/></linearGradient></defs>
    <path d="M0 75 Q600 -45 1200 20 L1200 700 Q620 830 0 675 Z" fill="url(#svcBlue)"/>
    <path d="M0 75 Q300 10 620 5 Q300 25 0 95 Z" fill="var(--green-light)"/>
    <path d="M1200 690 Q900 780 560 780 Q900 765 1200 715 Z" fill="var(--green-light)"/>
  </svg>
  <h2 class="abs services-title">OUR SERVICES</h2>
  <svg class="abs" style="left:430px;top:1654px" width="340" height="340" viewBox="0 0 340 340">
    <circle cx="170" cy="170" r="164" fill="none" stroke="#fff" stroke-width="2" stroke-dasharray="8 7"/>
    <g fill="var(--lime)"><circle cx="138" cy="7" r="6"/><circle cx="202" cy="7" r="6"/><circle cx="57" cy="53" r="6"/><circle cx="283" cy="53" r="6"/><circle cx="6" cy="170" r="6"/><circle cx="334" cy="170" r="6"/><circle cx="57" cy="287" r="6"/><circle cx="283" cy="287" r="6"/><circle cx="138" cy="333" r="6"/><circle cx="202" cy="333" r="6"/></g>
  </svg>
  <div class="abs hub"><b>Valmora Health</b></div>

  <div class="abs svc left" style="left:131px;top:1575px;width:352px">
    <div><h3>General Health Visits</h3><p>Sed ut perspiciatis unde omnis iste natus error sit voluptatem accusantium doloremque laudantium, totam rem</p></div>
    <div class="svc-icon"><svg width="44" height="44" viewBox="0 0 44 44" fill="none" stroke="#fff" stroke-width="2.2"><circle cx="20" cy="13" r="8"/><path d="M6 40c0-9 6-14 14-14s14 5 14 14"/><circle cx="33" cy="32" r="7" fill="#5fae2e"/><path d="M33 28v8M29 32h8"/></svg></div>
  </div>
  <div class="abs svc left" style="left:61px;top:1747px;width:349px">
    <div><h3>Vaccinations</h3><p>Sed ut perspiciatis unde omnis iste natus error sit voluptatem accusantium doloremque laudantium, totam rem</p></div>
    <div class="svc-icon"><svg width="44" height="44" viewBox="0 0 44 44" fill="none" stroke="#fff" stroke-width="2.2"><path d="M22 4 38 10v12c0 10-7 16-16 19C13 38 6 32 6 22V10z"/><path d="m14 30 14-14M24 12l8 8M16 24l4 4"/></svg></div>
  </div>
  <div class="abs svc left" style="left:123px;top:1919px;width:352px">
    <div><h3>Medical Imaging</h3><p>Sed ut perspiciatis unde omnis iste natus error sit voluptatem accusantium doloremque laudantium, totam rem</p></div>
    <div class="svc-icon"><svg width="44" height="44" viewBox="0 0 44 44" fill="none" stroke="#fff" stroke-width="2.2"><rect x="5" y="12" width="34" height="26" rx="3"/><path d="M16 12V7h12v5M22 18v14M15 25h14"/></svg></div>
  </div>
  <div class="abs svc" style="left:719px;top:1575px;width:362px">
    <div class="svc-icon"><svg width="44" height="44" viewBox="0 0 44 44" fill="none" stroke="#fff" stroke-width="2.2"><rect x="8" y="6" width="28" height="34" rx="3"/><path d="M16 6V3h12v3M14 16h16M14 23h16M14 30h10"/></svg></div>
    <div><h3>Physical Exams</h3><p>Sed ut perspiciatis unde omnis iste natus error sit voluptatem accusantium doloremque laudantium, totam rem</p></div>
  </div>
  <div class="abs svc" style="left:784px;top:1747px;width:359px">
    <div class="svc-icon"><svg width="44" height="44" viewBox="0 0 44 44" fill="none" stroke="#fff" stroke-width="2.2"><path d="M16 4h12M18 4v12L8 36c-1 2 0 4 2 4h24c2 0 3-2 2-4L26 16V4"/><path d="M12 28h20"/></svg></div>
    <div><h3>Additional Lab Testing</h3><p>Sed ut perspiciatis unde omnis iste natus error sit voluptatem accusantium doloremque laudantium, totam rem</p></div>
  </div>
  <div class="abs svc" style="left:727px;top:1919px;width:360px">
    <div class="svc-icon"><svg width="44" height="44" viewBox="0 0 44 44" fill="none" stroke="#fff" stroke-width="2.2"><circle cx="22" cy="13" r="8"/><path d="M6 40c0-9 7-14 16-14s16 5 16 14"/><path d="M17 32v5M14 35h6"/></svg></div>
    <div><h3>Diagnostic Testing</h3><p>Sed ut perspiciatis unde omnis iste natus error sit voluptatem accusantium doloremque laudantium, totam rem</p></div>
  </div>

  <div class="abs eyebrow" style="left:143px;top:2327px">Valmora Health</div>
  <h2 class="abs section-title" style="left:143px;top:2362px">Employers</h2>
  <p class="abs body-copy" style="left:143px;top:2430px;width:340px">Sed ut perspiciatis unde omnis iste natus error sit voluptatem accusantium doloremque laudtium, totam rem aperiam, eaque ipsa quae ab illo inventore veritatis et quasi architecto beatae vitae dicta sunt explicabo. Nemo enim ipsam voluptatem quia voluptas sit aspernatur aut odit aut fugit, sed quia consequuntur magni dolores eos qui ratione voluptatem sequi</p>
  <div class="abs btn-blue" style="left:143px;top:2637px;width:150px;height:42px;font-size:13px">LEARN MORE</div>
  <div class="abs video-frame"></div>
  <div class="abs video" role="img" aria-label="Doctor with a tablet consulting a young male patient"></div>
  <div class="abs play"><svg width="18" height="20" viewBox="0 0 18 20"><path d="M2 1v18l15-9z" fill="#9aa5ad"/></svg></div>

  <svg class="abs testi-band" viewBox="0 0 1200 620" preserveAspectRatio="none">
    <defs><linearGradient id="tGreen" x1="0" y1="0" x2="1" y2="0"><stop offset="0" stop-color="#1f8e3a"/><stop offset="1" stop-color="#2b9a3e"/></linearGradient></defs>
    <path d="M0 80 Q600 -20 1200 50 L1200 560 Q600 640 0 545 Z" fill="url(#tGreen)"/>
    <path d="M0 80 Q500 -5 900 15 Q500 10 0 100 Z" fill="var(--lime)"/>
  </svg>
  <h2 class="abs center-title" style="top:2865px;color:#fff">What Our Customers Say</h2>
  <div class="abs rule" style="left:571px;top:2931px;background:#fff"></div>
  <div class="abs t-card" style="left:164px">
    <span class="qmark">“</span>
    <p>Nemo enim ipsam voluptatem quia voluptas sit aspernatur aut odit aut fugit, sed quia consequuntur magni dolores eos qui ratione voluptatem sequi nesciunt. Neque porro quisquam est, qui dolorem ipsum quia dolor sit amet, consectetur, adipisci velit, sed quia non</p>
    <div class="t-person"><div class="avatar" role="img" aria-label="Customer portrait"></div><div><b>Maren Holt</b><span>Valmora Health</span><div class="stars">★★★★★</div></div></div>
    <span class="qend">”</span>
  </div>
  <div class="abs t-card" style="left:627px">
    <span class="qmark">“</span>
    <p>Nemo enim ipsam voluptatem quia voluptas sit aspernatur aut odit aut fugit, sed quia consequuntur magni dolores eos qui ratione voluptatem sequi nesciunt. Neque porro quisquam est, qui dolorem ipsum quia dolor sit amet, consectetur, adipisci velit, sed quia non</p>
    <div class="t-person"><div class="avatar" role="img" aria-label="Customer portrait"></div><div><b>Maren Holt</b><span>Valmora Health</span><div class="stars">★★★★★</div></div></div>
    <span class="qend">”</span>
  </div>
  <svg class="abs" style="left:578px;top:3277px" width="44" height="28" viewBox="0 0 44 28" fill="none" stroke="#fff" stroke-width="3"><path d="M14 3 4 14l10 11M30 3l10 11-10 11"/></svg>

  <h2 class="abs center-title" style="top:3432px;color:var(--ink)">Latest Blog</h2>
  <div class="abs rule" style="left:563px;top:3506px;width:74px;background:var(--green-light)"></div>

  <article class="abs blog-card" style="left:143px">
    <div class="blog-img" role="img" aria-label="Smiling nurse wearing a headset" style="background:linear-gradient(135deg,#cfe0ec,#6e9ac0 60%,#365f8c)"></div>
    <div class="blog-body">
      <div class="blog-date"><svg width="12" height="12" viewBox="0 0 12 12"><rect x="1" y="2" width="10" height="9" fill="none" stroke="#333" stroke-width="1.4"/><path d="M1 5h10M4 0v3M8 0v3" stroke="#333" stroke-width="1.4"/></svg>FEB 13, 2021</div>
      <h4>Nemo enim ipsam volup<br>quia voluptas sit</h4>
      <p>Sed ut perspiciatis unde omnis iste natus error sit voluptatem acsntium domque laudantium, totam</p>
      <span class="btn-outline">LEARN MORE</span>
    </div>
  </article>
  <article class="abs blog-card" style="left:455px">
    <div class="blog-img" role="img" aria-label="Children in a pediatric clinic waiting room" style="background:linear-gradient(135deg,#e4ecf2,#a9c3d6 55%,#5a86a8)"></div>
    <div class="blog-body">
      <div class="blog-date"><svg width="12" height="12" viewBox="0 0 12 12"><rect x="1" y="2" width="10" height="9" fill="none" stroke="#333" stroke-width="1.4"/><path d="M1 5h10M4 0v3M8 0v3" stroke="#333" stroke-width="1.4"/></svg>FEB 13, 2021</div>
      <h4>Nemo enim ipsam volup<br>quia voluptas sit</h4>
      <p>Sed ut perspiciatis unde omnis iste natus error sit voluptatem acsntium domque laudantium, totam</p>
      <span class="btn-outline">LEARN MORE</span>
    </div>
  </article>
  <article class="abs blog-card" style="left:770px">
    <div class="blog-img" role="img" aria-label="Doctors talking in a bright clinic hallway" style="background:linear-gradient(135deg,#eef1f2,#c3cdd4 55%,#7a8d99)"></div>
    <div class="blog-body">
      <div class="blog-date"><svg width="12" height="12" viewBox="0 0 12 12"><rect x="1" y="2" width="10" height="9" fill="none" stroke="#333" stroke-width="1.4"/><path d="M1 5h10M4 0v3M8 0v3" stroke="#333" stroke-width="1.4"/></svg>FEB 13, 2021</div>
      <h4>Nemo enim ipsam volup<br>quia voluptas sit</h4>
      <p>Sed ut perspiciatis unde omnis iste natus error sit voluptatem acsntium domque laudantium, totam</p>
      <span class="btn-outline">LEARN MORE</span>
    </div>
  </article>

  <footer class="abs footer"></footer>

  <svg class="abs quote-band" viewBox="0 0 1200 640" preserveAspectRatio="none">
    <defs><linearGradient id="qBlue" x1="0" y1="0" x2="1" y2="1"><stop offset="0" stop-color="#0b5aa8"/><stop offset="1" stop-color="#0a3f86"/></linearGradient></defs>
    <path d="M0 60 Q600 -40 1200 50 L1200 560 Q600 680 0 560 Z" fill="url(#qBlue)"/>
    <path d="M0 60 Q600 -40 1200 50 Q600 -20 0 80 Z" fill="var(--blue-light)"/>
    <path d="M60 600 Q600 660 1140 580 Q600 640 60 600 Z" fill="var(--blue-light)"/>
  </svg>
  <h2 class="abs center-title" style="top:4196px;color:#fff">Request A Quote</h2>
  <div class="abs rule" style="left:561px;top:4262px;width:78px;background:#fff"></div>
  <div class="abs field" style="left:307px;top:4307px;width:283px;height:47px">First Name *</div>
  <div class="abs field" style="left:610px;top:4307px;width:283px;height:47px">Last Name *</div>
  <div class="abs field" style="left:307px;top:4375px;width:586px;height:47px">Phone *</div>
  <div class="abs field" style="left:307px;top:4442px;width:586px;height:47px">E-mail Address</div>
  <div class="abs field" style="left:307px;top:4508px;width:586px;height:80px">Message</div>
  <div class="abs submit">SUBMIT</div>

  <div class="abs footer-logo">Valmora Health</div>
  <p class="abs footer-copy" style="left:128px;top:4908px;width:304px;text-align:center">Excepteur sint occaecat cupidatat non proident, sunt in culpa qui Nemo enim ipsam voluptatem</p>
  <div class="abs social" style="left:204px;top:4983px"><span></span><span></span><span></span><span></span></div>

  <h5 class="abs footer-heading" style="left:475px;top:4818px">CONTACT US</h5>
  <div class="abs contact-row" style="left:475px;top:4865px;width:260px">
    <svg width="18" height="22" viewBox="0 0 18 22" fill="none" stroke="#d9d9d9" stroke-width="1.6"><path d="M9 21s7-7 7-12A7 7 0 0 0 2 9c0 5 7 12 7 12z"/><circle cx="9" cy="9" r="2.5"/></svg>
    <div>Valmora Health<br>PO Box 214<br>enim ipsam voluptatem</div>
  </div>
  <div class="abs contact-row" style="left:475px;top:4948px;width:260px">
    <svg width="18" height="18" viewBox="0 0 24 24"><path fill="none" stroke="#d9d9d9" stroke-width="1.8" d="M6.6 10.8a15.1 15.1 0 0 0 6.6 6.6l2.2-2.2c.3-.3.7-.4 1-.2 1.1.4 2.3.6 3.6.6.6 0 1 .4 1 1V20c0 .6-.4 1-1 1A17 17 0 0 1 3 4c0-.6.4-1 1-1h3.5c.6 0 1 .4 1 1 0 1.3.2 2.5.6 3.6.1.3 0 .7-.2 1z"/></svg>
    <div>Phone :<br>888 555 0190</div>
  </div>
  <div class="abs contact-row" style="left:475px;top:5010px;width:300px">
    <svg width="20" height="16" viewBox="0 0 20 16" fill="none" stroke="#d9d9d9" stroke-width="1.6"><rect x="1" y="1" width="18" height="14"/><path d="m1 1 9 8 9-8"/></svg>
    <div>Email :<br>info@valmorahealth.example</div>
  </div>

  <h5 class="abs footer-heading" style="left:752px;top:4818px">SIGN UP TO RECEIVE EMAIL</h5>
  <p class="abs footer-copy" style="left:752px;top:4862px;width:310px">Excepteur sint occaecat cupidatat non proident, sunt in culpa qui Nemo enim</p>
  <div class="abs email-box">Enter Email
    <span class="email-go"><svg width="16" height="16" viewBox="0 0 16 16"><path d="M1 7 15 1 9 15 7 9z" fill="#fff"/></svg></span>
  </div>

  <div class="abs copyright">Copyright © Valmora Health 2021. All rights reserved. | Privacy Policy</div>
</div>
</body>
</html>
```